Local News Website

We are looking for a innovative design for our local news portal. The current design can be found on http://www.velmora.nl.

It should include a frontpage, article view and listpage of video's and picture galleries.

We want a fresh design based (or like) on a Metro look.

For inspiration:
http://brinqua.com/
http://tarnwick.dovemarsh.com/
http://pemrugo.nl

-
Current design:
Picture gallaries overview:
http://www.velmora.nl/mediatheek/

Videolist overview:
http://www.velmora.nl/mediatheek/televisiegemist/127/velmorajournaal/

We are committed to get this contest to work, so give us your best design and we will make a fast decision.

Target Market(s)

There is no specific target market just a general audience.

Industry/Entity Type

News

Requirements
Must have
• - Videoplayer (or breaking news article) placement on frontpage.
- The traditional content elements from any news site

• Text articles
• Video / Audio (seperated and in a text article)
• Pictures & picture galleries (seperated and in a text article)
• Sections (News, Sport Business, Entertainment etc) (has to take up minimum of 7 sections).

The design needs to make sense for the average user, great usability.

Social engagement should be integral, the depth of integration is up to each designer.

```html
<!DOCTYPE html>
<html lang="nl">
<head>
<meta charset="utf-8">
<title>Velmora – Nieuws</title>
<link rel="stylesheet" href="https://fonts.googleapis.com/css2?family=PT+Sans+Narrow:wght@400;700&display=swap">
<style>
:root{
  --navy:#0f2466;
  --navy-text:#12275e;
  --teal:#1f7d8a;
  --teal-light:#45a9bf;
  --link:#17708a;
  --red-title:#d9453a;
  --line:#b9bcc0;
  --panel-top:#fafafa;
  --panel-bottom:#ececec;
  --icon:#dcdcdc;
  --f1:#d5342a;--f2:#da3b2e;--f3:#df4133;--f4:#e44739;--f5:#e94e40;--f6:#ef5647;
  --f-bottom:#d83629;
  --f-meta:#f6b0a6;
}
*{margin:0;padding:0;box-sizing:border-box}
html,body{width:897px;height:1200px;overflow:hidden;background:#fff}
body{position:relative;font-family:"PT Sans Narrow","Arial Narrow",sans-serif;color:#222}
.abs{position:absolute}

.site-header{left:0;top:0;width:897px;height:68px;background:#fff}
.brand{left:22px;top:14px;font-size:34px;font-weight:400;color:var(--navy-text);line-height:40px}

.band{left:0;top:68px;width:897px;height:307px;background:var(--navy)}
.main-nav{right:16px;top:91px;display:flex;height:40px}
.main-nav a{color:var(--teal-light);text-decoration:none;font-size:16px;padding:0 9px;line-height:40px}
.main-nav a.active{background:var(--teal);color:#fff;border-radius:3px 3px 0 0}

.hero{left:10px;top:131px;width:877px;height:314px;box-shadow:0 6px 14px rgba(0,0,0,.18);
  background:linear-gradient(90deg,#7c8590 0%,#a7a39c 22%,#c7544a 45%,#b94a43 60%,#7d5a3e 78%,#3e3a32 100%)}
.hero-title{left:35px;top:176px;font-size:20px;font-weight:400;color:#111}
.hero-lead{left:35px;top:217px;width:310px;font-size:14px;line-height:19px;color:#111}
.hero-pager{right:18px;top:414px;color:#fff;font-size:12px}
.hero-pager b{font-size:18px;font-weight:400}

.media-panel{left:9px;top:482px;width:878px;height:199px;border:1px solid #e1e1e1;border-radius:4px;
  background:linear-gradient(var(--panel-top),var(--panel-bottom))}
.media-item{top:495px;width:140px}
.media-item svg{display:block;margin:0 auto;height:88px}
.media-item h3{font-size:11px;color:var(--red-title);font-weight:700;text-align:center;margin-top:18px;text-transform:uppercase}
.media-item p{font-size:9.5px;line-height:13px;color:var(--link);margin-top:3px}

.section-row{left:21px;width:857px;height:62px;border-bottom:1px solid var(--line)}
.section-row h2{position:absolute;left:8px;top:20px;font-size:20px;font-weight:400;color:var(--navy-text)}
.section-row .divider{position:absolute;left:102px;top:0;width:1px;height:61px;background:var(--line)}
.section-row p{position:absolute;top:10px;width:135px;font-size:9.5px;line-height:13px;color:var(--link)}

.footer{left:0;top:995px;width:897px;height:205px;background:var(--f-bottom)}
.f-col{top:995px;height:135px;padding:24px 0 0 0;font-size:11px;line-height:14.8px;color:#fff}
.f-col ul{list-style:none}
.footer-meta{right:27px;top:1154px;font-size:8px;color:var(--f-meta);text-align:right}
.footer-links{right:329px;top:1178px;font-size:8px;color:var(--f-meta)}
</style>
</head>
<body>

<header class="site-header abs">
  <div class="brand abs">Velmora</div>
</header>

<div class="band abs"></div>
<nav class="main-nav abs">
  <a class="active" href="#">Nieuws</a><a href="#">Televisie</a><a href="#">Radio</a><a href="#">Internet</a><a href="#">Over VELMORA</a>
</nav>

<div class="hero abs" role="img" aria-label="Foto: vrouw in rode trui leest de krant achter een caféraam"></div>
<h1 class="hero-title abs">Pim van Daalen signeert zijn boek</h1>
<p class="hero-lead abs">In 1995 emigreerde Lindhovenaar Pim van Daalen met vrouw en twee dochters naar Canada. Lees meer...</p>
<div class="hero-pager abs"><b>1</b> 2 3 4 5</div>

<div class="media-panel abs"></div>

<div class="media-item abs" style="left:35px">
  <svg viewBox="0 0 100 80"><rect x="2" y="2" width="96" height="74" rx="8" fill="var(--icon)"/><rect x="10" y="10" width="62" height="56" rx="10" fill="#f3f3f3"/><rect x="78" y="14" width="14" height="30" fill="#ececec"/><circle cx="85" cy="62" r="3" fill="#cfcfcf"/></svg>
  <h3>Video's bekijken</h3>
  <p>Muziekvereniging Aurora uit Heelmond-Oost huldigde op zaterdag 14 april zes jubilarissen. Lees meer...</p>
</div>
<div class="media-item abs" style="left:207px">
  <svg viewBox="0 0 100 80"><path d="M30 10h40l6 10h16a6 6 0 0 1 6 6v46a6 6 0 0 1-6 6H8a6 6 0 0 1-6-6V26a6 6 0 0 1 6-6h16z" fill="var(--icon)"/><circle cx="50" cy="48" r="22" fill="#f3f3f3"/><circle cx="50" cy="48" r="15" fill="var(--icon)"/></svg>
  <h3>Foto's bekijken</h3>
  <p>Muziekvereniging Aurora uit Heelmond-Oost huldigde op zaterdag 14 april zes jubilarissen. Lees meer...</p>
</div>
<div class="media-item abs" style="left:390px">
  <svg viewBox="0 0 100 100"><g transform="rotate(-18 50 50)"><rect x="25" y="2" width="50" height="96" fill="var(--icon)"/><g fill="#f4f4f4"><rect x="28" y="8" width="6" height="8"/><rect x="28" y="24" width="6" height="8"/><rect x="28" y="40" width="6" height="8"/><rect x="28" y="56" width="6" height="8"/><rect x="28" y="72" width="6" height="8"/><rect x="66" y="8" width="6" height="8"/><rect x="66" y="24" width="6" height="8"/><rect x="66" y="40" width="6" height="8"/><rect x="66" y="56" width="6" height="8"/><rect x="66" y="72" width="6" height="8"/><rect x="38" y="8" width="24" height="26"/><rect x="38" y="40" width="24" height="26"/><rect x="38" y="72" width="24" height="22"/></g></g></svg>
  <h3>Video's bekijken</h3>
  <p>Muziekvereniging Aurora uit Heelmond-Oost huldigde op zaterdag 14 april zes jubilarissen. Lees meer...</p>
</div>
<div class="media-item abs" style="left:557px">
  <svg viewBox="0 0 100 100"><g fill="var(--icon)" transform="translate(50 50)"><rect x="-8" y="-46" width="16" height="20"/><rect x="-8" y="-46" width="16" height="20" transform="rotate(45)"/><rect x="-8" y="-46" width="16" height="20" transform="rotate(90)"/><rect x="-8" y="-46" width="16" height="20" transform="rotate(135)"/><rect x="-8" y="-46" width="16" height="20" transform="rotate(180)"/><rect x="-8" y="-46" width="16" height="20" transform="rotate(225)"/><rect x="-8" y="-46" width="16" height="20" transform="rotate(270)"/><rect x="-8" y="-46" width="16" height="20" transform="rotate(315)"/><circle r="32"/></g><circle cx="50" cy="50" r="14" fill="#f3f3f3"/></svg>
  <h3>Bekijken</h3>
  <p>Muziekvereniging Aurora uit Heelmond-Oost huldigde op zaterdag 14 april zes jubilarissen. Lees meer...</p>
</div>
<div class="media-item abs" style="left:720px">
  <svg viewBox="0 0 100 90"><path d="M8 60V48a42 42 0 0 1 84 0v12" fill="none" stroke="var(--icon)" stroke-width="8"/><rect x="2" y="52" width="20" height="36" rx="8" fill="var(--icon)"/><rect x="78" y="52" width="20" height="36" rx="8" fill="var(--icon)"/><polyline points="24,70 32,70 36,50 42,86 48,46 54,84 60,54 66,76 76,70" fill="none" stroke="var(--icon)" stroke-width="3"/></svg>
  <h3>Radio</h3>
  <p>Muziekvereniging Aurora uit Heelmond-Oost huldigde op zaterdag 14 april zes jubilarissen. Lees meer...</p>
</div>

<section class="section-row abs" style="top:695px">
  <h2>NIEUWSLIJN</h2><span class="divider"></span>
  <p style="left:119px">Muziekvereniging Aurora uit Heelmond-Oost huldigde op zaterdag 14 april zes jubilarissen. Lees meer...</p>
  <p style="left:303px">Muziekvereniging Aurora uit Heelmond-Oost huldigde op zaterdag 14 april zes jubilarissen. Lees meer...</p>
  <p style="left:478px">Muziekvereniging Aurora uit Heelmond-Oost huldigde op zaterdag 14 april zes jubilarissen. Lees meer...</p>
  <p style="left:662px">Muziekvereniging Aurora uit Heelmond-Oost huldigde op zaterdag 14 april zes jubilarissen. Lees meer...</p>
</section>
<section class="section-row abs" style="top:800px">
  <h2>AGENDA</h2><span class="divider"></span>
  <p style="left:119px">Muziekvereniging Aurora uit Heelmond-Oost huldigde op zaterdag 14 april zes jubilarissen. Lees meer...</p>
  <p style="left:303px">Muziekvereniging Aurora uit Heelmond-Oost huldigde op zaterdag 14 april zes jubilarissen. Lees meer...</p>
  <p style="left:478px">Muziekvereniging Aurora uit Heelmond-Oost huldigde op zaterdag 14 april zes jubilarissen. Lees meer...</p>
  <p style="left:662px">Muziekvereniging Aurora uit Heelmond-Oost huldigde op zaterdag 14 april zes jubilarissen. Lees meer...</p>
</section>
<section class="section-row abs" style="top:905px">
  <h2>SPORTLIJN</h2><span class="divider"></span>
  <p style="left:119px">Muziekvereniging Aurora uit Heelmond-Oost huldigde op zaterdag 14 april zes jubilarissen. Lees meer...</p>
  <p style="left:303px">Muziekvereniging Aurora uit Heelmond-Oost huldigde op zaterdag 14 april zes jubilarissen. Lees meer...</p>
  <p style="left:478px">Muziekvereniging Aurora uit Heelmond-Oost huldigde op zaterdag 14 april zes jubilarissen. Lees meer...</p>
  <p style="left:662px">Muziekvereniging Aurora uit Heelmond-Oost huldigde op zaterdag 14 april zes jubilarissen. Lees meer...</p>
</section>

<footer class="footer abs"></footer>
<div class="f-col abs" style="left:0;width:131px;background:var(--f1);padding-left:36px"><ul><li>Nieuws</li><li>NieuwsLijn</li><li>Nieuwsredatie</li><li>Upload uw bijdrage</li><li>Tip de redactie</li><li>Microblog</li><li>RSS</li></ul></div>
<div class="f-col abs" style="left:131px;width:131px;background:var(--f2);padding-left:27px"><ul><li>Televisie</li><li>Televisiegids</li><li>Uitzending gemist</li><li>Videokanaal</li></ul></div>
<div class="f-col abs" style="left:262px;width:130px;background:var(--f3);padding-left:28px"><ul><li>Radio</li><li>Radiogids</li><li>Livestream</li><li>Uitzending gemist</li></ul></div>
<div class="f-col abs" style="left:392px;width:130px;background:var(--f4);padding-left:20px"><ul><li>Internet</li><li>Mobiel</li><li>Podcasting</li><li>Vodcasting</li><li>Toegankelijkheids hulp</li><li>Privacy &amp; Cookies</li><li>A - Z</li></ul></div>
<div class="f-col abs" style="left:522px;width:130px;background:var(--f5);padding-left:31px"><ul><li>Over VELMORA</li><li>Contact</li><li>Adverteren</li><li>Frequenties</li><li>Businessclub</li><li>Stage / Vacature</li></ul></div>
<div class="f-col abs" style="left:652px;width:245px;background:var(--f6)"></div>
<p class="footer-meta abs">VELMORA Publieke Lokale Media-instelling, design en ontwikkeling Tralvo Media: versie: 3.2 | Open Licentie [BY-NC-ND]</p>
<p class="footer-links abs">Disclaimer | Privacy</p>

</body>
</html>
```